Newsletter Ad

I am looking for someone to design an advertisement for a mother's club newsletter. 4" wide X by 5" tall (and 2.5" wide X 5" tall if possible).

I'm a psychotherapist, so want the ad to look professional, but modern. I have a logo with my photo attached that can be incorporated into the design. The colors of my website are turquoise and white. I'd like to keep with that theme...so maybe some turquoise blocking to match the logo font color.

I'm uploading a logo as well as an ad draft with the content I'd like listed in the ad.

```html
<!DOCTYPE html>
<html lang="en">
<head>
<meta charset="utf-8">
<title>Dana Morell, MA, MFT – Newsletter Ad</title>
<link href="https://fonts.googleapis.com/css2?family=Didact+Gothic&display=swap" rel="stylesheet">
<style>
  :root {
    --teal: #3a9b98;
    --teal-text: #2e9c9a;
    --paper-grey: #9c9c9c;
    --ink: #1c1c1c;
    --rule: #3a3a3a;
    --white: #ffffff;
    --night: #141414;
  }
  html, body {
    margin: 0;
    padding: 0;
    width: 961px;
    height: 1200px;
    overflow: hidden;
    background: var(--white);
  }
  .ad {
    position: relative;
    width: 961px;
    height: 1200px;
    overflow: hidden;
    font-family: "Didact Gothic", "Century Gothic", sans-serif;
    background: var(--paper-grey);
  }
  .portrait {
    position: absolute;
    left: 0; top: 0;
    width: 301px; height: 474px;
    background: linear-gradient(160deg, #2a2a2a 0%, #7a5a44 40%, #c79e80 60%, #3a3a3a 100%);
  }
  .side-pattern {
    position: absolute;
    left: 0; top: 474px;
    width: 301px; height: 726px;
    background: linear-gradient(180deg, #1a1a1a 0%, var(--night) 100%);
  }
  .band {
    position: absolute;
    left: 301px;
    width: 660px;
    box-sizing: border-box;
    text-align: center;
  }
  .band-top { top: 0; height: 64px; background: var(--paper-grey); }
  .band-name {
    top: 64px; height: 110px;
    background: var(--white);
    display: flex; align-items: center; justify-content: center;
  }
  .name {
    margin: 0;
    font-size: 55px;
    font-weight: 400;
    color: var(--teal-text);
    letter-spacing: 0.5px;
  }
  .band-service {
    top: 174px; height: 207px;
    background: var(--paper-grey);
    color: var(--ink);
    padding-top: 34px;
    border-bottom: 3px solid var(--rule);
  }
  .service-title { margin: 0; font-size: 52px; font-weight: 400; line-height: 1.1; }
  .service-sub { margin: 8px 0 0; font-size: 30px; line-height: 1.35; }
  .band-focus {
    top: 384px; height: 529px;
    background: var(--teal);
    border-bottom: 3px solid var(--rule);
    padding-top: 22px;
  }
  .focus-list {
    list-style: none; margin: 0; padding: 0;
    color: var(--white);
    font-size: 35px;
    line-height: 60px;
  }
  .band-contact {
    top: 916px; height: 204px;
    background: var(--paper-grey);
    color: var(--ink);
    padding-top: 20px;
    border-bottom: 3px solid var(--rule);
    font-size: 29px;
    line-height: 46px;
  }
  .band-contact p { margin: 0; }
  .band-license {
    top: 1123px; height: 77px;
    background: var(--teal);
    text-align: right;
    padding: 22px 24px 0 0;
    font-size: 21px;
    color: var(--ink);
  }
</style>
</head>
<body>
  <main class="ad">
    <div class="portrait" role="img" aria-label="Portrait photograph of the therapist"></div>
    <div class="side-pattern" role="img" aria-label="Dark geometric triangle pattern"></div>

    <div class="band band-top"></div>
    <header class="band band-name">
      <h1 class="name">DANA MORELL, MA, MFT</h1>
    </header>

    <section class="band band-service">
      <h2 class="service-title">Psychotherapy</h2>
      <p class="service-sub">for Individuals,<br>Couples and Families</p>
    </section>

    <section class="band band-focus">
      <ul class="focus-list">
        <li>Parenting</li>
        <li>Depression</li>
        <li>Anxiety</li>
        <li>Life Transitions</li>
        <li>Divorce</li>
        <li>Couples Issues</li>
        <li>Women’s Issues</li>
        <li>Attachment and Neuroscience</li>
      </ul>
    </section>

    <address class="band band-contact" style="font-style:normal">
      <p>418 Alder Lane, Fairhaven, CA 94870</p>
      <p>www.danamorell.com</p>
      <p>dana@danamorell.com</p>
      <p>555.210.3846</p>
    </address>

    <footer class="band band-license">License# MFC48213</footer>
  </main>
</body>
</html>
```